Personal Chef Business Card Design

My company, Simmered, is a personal in-home chef service that caters to clients' needs, but I am not a caterer. The types of services that I provide range from : weekly menus for busy families, special menus for specific diets, custom menus, private parties, intimate dinners, and brunch parties. My cooking style is seasonal and simple with the option of a variety of cuisines. I like colorful and simple business cards. My business is just getting started as I will be the only employee for now. I would like to be able to use the design on the card for my logo also. I don't know if logo design is a different service altogether.

If you can convince me to go with double-sided, then so be it, but until then, I'll stick with singe-sided.

Target Market(s)

busy families, health conscious, private parties, brunch parties, dinner parties

Industry/Entity Type

Chef

Contact Information for Business Card

Owen Talbot
owentalbot@kestrelmail.com
555-418-2937
Simmered Personal Chef Service
Serving the DC/VA/MD area

Font styles to use
Serif
Sans Serif
Decorative
Script
Other font styles liked:
• Anything

Requirements
Must have
• I will be using the illustration as my logo so that I can use it for promotional merchandise.

```html
<!DOCTYPE html>
<html lang="en">
<head>
<meta charset="utf-8">
<title>Simmered – Business Card</title>
<link href="https://fonts.googleapis.com/css2?family=Open+Sans:wght@400;600;700&display=swap" rel="stylesheet">
<style>
  :root {
    --backdrop: #1c1c1c;
    --card-front: #fdd86e;
    --card-back: #951b20;
    --brand-red: #951b20;
    --text-grey: #4a4a4a;
    --mark-light: #ececec;
    --white: #ffffff;
  }
  * { margin: 0; padding: 0; box-sizing: border-box; }
  html, body {
    width: 1200px;
    height: 900px;
    overflow: hidden;
    background: var(--backdrop);
    font-family: "Open Sans", Arial, sans-serif;
  }
  .canvas {
    position: relative;
    width: 1200px;
    height: 900px;
  }
  .card {
    position: absolute;
    border-radius: 14px;
  }
  .card--front {
    left: 152px; top: 309px;
    width: 432px; height: 250px;
    background: var(--card-front);
  }
  .card--back {
    left: 631px; top: 310px;
    width: 435px; height: 252px;
    background: var(--card-back);
  }

  /* brand block */
  .brand {
    position: absolute;
    display: flex;
    flex-direction: column;
    align-items: center;
  }
  .brand__square { display: block; }
  .brand__name {
    font-weight: 400;
    letter-spacing: 1px;
    line-height: 1;
    text-transform: uppercase;
  }
  .card--front .brand {
    left: 22px; top: 81px; width: 186px;
  }
  .card--front .brand__square {
    width: 52px; height: 52px;
    background: var(--brand-red);
  }
  .card--front .brand__name {
    margin-top: 12px;
    font-size: 29px;
    color: var(--brand-red);
  }
  .card--back .brand {
    left: 0; top: 67px; width: 410px;
  }
  .card--back .brand__square {
    width: 66px; height: 66px;
    background: var(--mark-light);
    border-radius: 2px;
  }
  .card--back .brand__name {
    margin-top: 14px;
    font-size: 36px;
    color: var(--white);
  }

  /* contact details */
  .details {
    position: absolute;
    left: 229px; top: 47px;
    color: var(--text-grey);
    font-size: 12.5px;
    line-height: 15px;
    white-space: nowrap;
  }
  .details__name {
    font-size: 17.5px;
    font-weight: 700;
    color: var(--brand-red);
    line-height: 22px;
  }
  .details__role { margin-bottom: 11px; }
  .details__address { margin-bottom: 12px; }
  .contact-list { list-style: none; }
  .contact-list li {
    display: flex;
    align-items: center;
    height: 16px;
  }
  .contact-list svg {
    width: 9px; height: 9px;
    margin-right: 8px;
    fill: var(--brand-red);
    flex: none;
  }
</style>
</head>
<body>
<div class="canvas">

  <section class="card card--front" aria-label="Business card front">
    <div class="brand">
      <span class="brand__square"></span>
      <span class="brand__name">Simmered</span>
    </div>

    <div class="details">
      <p class="details__name">Owen Talbot</p>
      <p class="details__role">Managing Director</p>
      <p class="details__address">1234, Address Goes Here<br>Country Name, 123456</p>
      <ul class="contact-list">
        <li>
          <svg viewBox="0 0 10 10" aria-hidden="true"><path d="M3 0h4a1 1 0 0 1 1 1v8a1 1 0 0 1-1 1H3a1 1 0 0 1-1-1V1a1 1 0 0 1 1-1zm0 1.5v6h4v-6z"/></svg>
          555-418-2937
        </li>
        <li>
          <svg viewBox="0 0 10 10" aria-hidden="true"><path d="M0 3.5Q5 0 10 3.5L8.5 5 7 4V3H3v1L1.5 5zM2 6l1.5-1.5h3L8 6v3H2z"/></svg>
          555-418-2937
        </li>
        <li>
          <svg viewBox="0 0 10 10" aria-hidden="true"><path d="M2.5 0h5v3h-5zM0 3.5h10V10H0zm2 2v1h2v-1zm4 0v1h2v-1z"/></svg>
          555-418-2937
        </li>
        <li>
          <svg viewBox="0 0 10 10" aria-hidden="true"><path d="M0 2h10v.8L5 6 0 2.8zm0 2l5 3.2L10 4v4H0z"/></svg>
          owentalbot@kestrelmail.com
        </li>
        <li>
          <svg viewBox="0 0 10 10" aria-hidden="true"><path d="M6 1l3 3-2 2-1-1 1-1-1-1-3 3 1 1-1 1-1-1-1-1zm-1.5 4.5l-1-1 3-3 1 1z"/></svg>
          www.simmeredchef.com
        </li>
      </ul>
    </div>
  </section>

  <section class="card card--back" aria-label="Business card back">
    <div class="brand">
      <span class="brand__square"></span>
      <span class="brand__name">Simmered</span>
    </div>
  </section>

</div>
</body>
</html>
```